Product packaging design for lentils

Looking to create a design for lentils in 4lb format. We are looking to create a base design for the bags, and then from there will have additional designs for the different products with different product name, barcodes and nutritional information.

Industry/Entity Type

Food

```html
<!DOCTYPE html>
<html lang="en">
<head>
<meta charset="UTF-8">
<title>Organic Red Lentils – 4lb Bag</title>
<link rel="stylesheet" href="https://fonts.googleapis.com/css2?family=Roboto+Slab:wght@400;500;600;700&display=swap">
<style>
  :root {
    --backdrop: #fffcee;
    --bag-black: #1e1d1f;
    --seal-black: #151416;
    --brand-red: #b71f2e;
    --accent-red: #c8283a;
    --lentil-orange: #e0703f;
    --lentil-light: #f0925e;
    --lentil-deep: #c9562c;
    --ink-white: #f6f4f2;
    --badge-green: #2f7d3a;
    --badge-blue: #1f5ba3;
  }
  * { margin: 0; padding: 0; box-sizing: border-box; }
  html, body {
    width: 1200px; height: 1200px; overflow: hidden;
    background: var(--backdrop);
    font-family: "Roboto Slab", Georgia, serif;
  }
  .canvas { position: relative; width: 1200px; height: 1200px; }
  .bag-art { position: absolute; left: 0; top: 0; }
  .brand {
    position: absolute; left: 0; width: 1208px; top: 322px;
    display: flex; justify-content: center; align-items: center; gap: 10px;
    color: var(--ink-white);
  }
  .brand-dot { width: 14px; height: 14px; border-radius: 50%; background: var(--ink-white); }
  .brand-name { font-size: 22px; font-weight: 600; letter-spacing: 0.5px; }
  .product-title {
    position: absolute; left: 0; width: 1172px; top: 392px;
    text-align: center; color: var(--ink-white);
  }
  .product-kicker { font-size: 43px; font-weight: 500; line-height: 1; letter-spacing: 0.5px; }
  .product-name { font-size: 61px; font-weight: 700; line-height: 1; margin-top: 8px; letter-spacing: 0.5px; }
  .product-tagline {
    display: flex; justify-content: center; align-items: center; gap: 10px;
    margin-top: 13px; font-size: 19px; font-weight: 500;
  }
  .product-tagline::before, .product-tagline::after {
    content: ""; width: 36px; height: 3px; background: var(--ink-white);
  }
  .protein-callout {
    position: absolute; left: 392px; top: 810px; width: 111px;
    border-top: 1px solid var(--accent-red); border-bottom: 1px solid var(--accent-red);
    text-align: center; padding: 8px 0 8px;
  }
  .protein-amount { color: var(--ink-white); font-size: 22px; line-height: 1.2; }
  .protein-label { color: var(--accent-red); font-size: 14.5px; line-height: 1.25; font-weight: 500; }
  .protein-unit { color: var(--ink-white); font-size: 15px; line-height: 1.2; }
  .net-weight {
    position: absolute; left: 397px; top: 964px;
    color: var(--ink-white); font-size: 15px; font-weight: 500; letter-spacing: 2.5px;
  }
</style>
</head>
<body>
<main class="canvas">
  <svg class="bag-art" width="1200" height="1200" viewBox="0 0 1200 1200">
    <defs>
      <linearGradient id="lentilTone" x1="0" y1="0" x2="1" y2="1">
        <stop offset="0" stop-color="var(--lentil-deep)"/>
        <stop offset="0.5" stop-color="var(--lentil-orange)"/>
        <stop offset="1" stop-color="var(--lentil-light)"/>
      </linearGradient>
    </defs>
    <rect class="bag-body" x="332" y="110" width="530" height="965" rx="22" fill="var(--bag-black)"/>
    <rect class="top-seal" x="332" y="110" width="530" height="102" rx="6" fill="var(--seal-black)"/>
    <rect class="lentil-window" x="606" y="212" width="254" height="794" fill="url(#lentilTone)"
          role="img" aria-label="Photo of dry red lentils filling the bag window"/>
    <path class="red-panel" fill="var(--brand-red)"
      d="M332,212 H776 C830,232 851,330 851,430 C851,522 792,590 730,592 C680,594 640,562 606,557
         C562,548 512,548 492,600 C455,690 425,733 372,735 L332,722 Z"/>
    <circle class="cert-badge" cx="691" cy="967" r="31" fill="var(--badge-green)"/>
    <circle cx="691" cy="967" r="25" fill="var(--ink-white)"/>
    <rect class="cert-badge" x="734" y="941" width="76" height="53" fill="var(--badge-blue)"/>
  </svg>

  <div class="brand">
    <span class="brand-dot"></span>
    <span class="brand-name">Sunfield Pantry</span>
  </div>

  <div class="product-title">
    <div class="product-kicker">ORGANIC</div>
    <div class="product-name">RED LENTILS</div>
    <div class="product-tagline">PREMIUM QUALITY</div>
  </div>

  <div class="protein-callout">
    <div class="protein-amount">11g</div>
    <div class="protein-label">PLANT-BASED<br>PROTEIN</div>
    <div class="protein-unit">per serving</div>
  </div>

  <div class="net-weight">NET WT. 4lb</div>
</main>
</body>
</html>
```